Hollow Mesa Farm Vault Reserve Wine Label (Front and Back)

I need to create an elite tier wine label.  I would like it to be in a light, natural color with silver or gold.  I would like it to look rich and expensive, mostly monochromatic, elegantly simple.  It will need to stand up next to wine labels that are black and charcoal colored and look like the more expensive wine of the 3.  I have attached a similar label that it will be grouped with and some instructions.
We are a winery in southeast Washington state with a reputation for fine wines and top notch terroir.  We want to present family, tradition and high value wine in the bottle.

```html
<!DOCTYPE html>
<html lang="en">
<head>
<meta charset="utf-8">
<title>Hollow Mesa Farm · Vault Reserve Label</title>
<link rel="stylesheet" href="https://fonts.googleapis.com/css2?family=Cinzel:wght@400;700&family=Cormorant+Garamond:wght@500;600&family=Great+Vibes&display=swap">
<style>
  :root {
    --backdrop: #2f2b29;
    --paper: #f4f4f2;
    --ink: #1c1c1c;
    --gold-dark: #c98a12;
    --gold-mid: #f2c230;
    --gold-light: #f9dd6e;
    --gold-script: #c58a2a;
  }
  * { margin: 0; padding: 0; box-sizing: border-box; }
  html, body {
    width: 1068px; height: 1200px; overflow: hidden;
    background: var(--backdrop);
  }
  .canvas {
    width: 1068px; height: 1200px;
    display: flex; align-items: center; justify-content: center;
  }
  .label {
    width: 650px; height: 1110px;
    background: var(--paper);
    display: flex; flex-direction: column; align-items: center;
    color: var(--ink);
    box-shadow: 0 10px 40px rgba(0,0,0,.35);
  }
  .gold-band {
    width: 100%;
    background: linear-gradient(90deg, var(--gold-dark), var(--gold-mid) 30%, var(--gold-light) 50%, var(--gold-mid) 70%, var(--gold-dark));
  }
  .gold-band--top { height: 26px; }
  .gold-band--bottom {
    margin-top: auto; height: 78px;
    display: flex; align-items: center; justify-content: center;
  }
  .motto {
    font-family: 'Cormorant Garamond', serif; font-weight: 600;
    font-size: 23px; letter-spacing: .2px; color: var(--ink);
  }
  .winery-name {
    margin-top: 82px;
    font-family: 'Cinzel', serif; font-weight: 400;
    font-size: 68px; line-height: 94px; text-align: center;
    letter-spacing: 1px;
  }
  .appellation {
    margin-top: 56px;
    font-family: 'Cormorant Garamond', serif; font-weight: 600;
    font-size: 31px; letter-spacing: 7px;
  }
  .brand-mark {
    margin-top: 60px; height: 200px;
    display: flex; align-items: center; gap: 18px;
  }
  .brand-mark__square {
    width: 46px; height: 46px;
    background: linear-gradient(135deg, var(--gold-dark), var(--gold-light) 50%, var(--gold-dark));
  }
  .brand-mark__name {
    font-family: 'Cinzel', serif; font-weight: 400;
    font-size: 34px; letter-spacing: 2px; color: var(--ink);
  }
  .vineyard {
    margin-top: 56px;
    font-family: 'Cormorant Garamond', serif; font-weight: 600;
    font-size: 32px; letter-spacing: 1.5px;
  }
  .tier {
    margin-top: 12px;
    font-family: 'Cinzel', serif; font-weight: 700;
    font-size: 62px; letter-spacing: 1px;
    text-shadow: 2px 2px 0 var(--gold-mid);
  }
  .varietal {
    margin-top: 4px;
    font-family: 'Great Vibes', cursive;
    font-size: 58px; color: var(--gold-script);
  }
  .vintage {
    margin-top: 14px;
    font-family: 'Cormorant Garamond', serif; font-weight: 600;
    font-size: 32px;
  }
</style>
</head>
<body>
  <main class="canvas">
    <article class="label">
      <div class="gold-band gold-band--top"></div>
      <h1 class="winery-name">HOLLOW MESA<br>FARM</h1>
      <p class="appellation">HORSE HEAVEN HILLS</p>
      <div class="brand-mark">
        <span class="brand-mark__square"></span>
        <span class="brand-mark__name">HOLLOW MESA FARM</span>
      </div>
      <p class="vineyard">ESTATE VINEYARD</p>
      <h2 class="tier">VAULT RESERVE</h2>
      <p class="varietal">Cabernet Sauvignon</p>
      <p class="vintage">2022</p>
      <div class="gold-band gold-band--bottom">
        <p class="motto">FAMILY STEWARDS OF THE LAND FOR 5 GENERATIONS</p>
      </div>
    </article>
  </main>
</body>
</html>
```